Laser Tattoo Removal Business Cards

We are looking for a professional business card design for a laser tattoo removal business. Ideally looking for a black business card design. The name of the business is Brightline Tattoo Removal. We place our cards at local tattoo shops so we ideally are looking for something trendy/edgy to draw both male and female clientele in.

Target Market(s)

Male/Female ages 18-60

Contact Information for Business Card

black background ideally.. hoping to stay within greys, whites and black

Font styles to use
Serif
Sans Serif

Colors
121212
a9a9a9
5c5c5c
f5f5f5
ffffff
7f7f7f
606060
848484
9d9d9d

Requirements
Must have
• Employee Info:
• Melissa Thornbury
• Chief Executive Offer
• m: 919.537.2846
• w: 919.362.4178
• f: 919.685.3907
• mthornbury@brightlinetattooremoval.example
• Address:
• 4615 Oakmere Pkwy, Suite 210
• Raleigh, NC 27654
• Website:
• www.brightlinetattooremoval.example
Nice to have
• Myabe business name on back or logo on back and employee info on the front

```html
<!DOCTYPE html>
<html lang="en">
<head>
<meta charset="utf-8">
<title>Brightline Tattoo Removal – Business Card</title>
<link rel="stylesheet" href="https://fonts.googleapis.com/css2?family=Roboto:wght@400;500&family=Roboto+Condensed:wght@400;700&display=swap">
<style>
  :root {
    --ink: #121212;
    --black: #000000;
    --paper: #f5f5f5;
    --white: #ffffff;
    --grey-light: #a9a9a9;
    --grey-mid: #9d9d9d;
    --grey-dark: #5c5c5c;
    --stage: #7f7f7f;
  }
  * { margin: 0; padding: 0; box-sizing: border-box; }
  html, body { width: 1200px; height: 960px; overflow: hidden; }
  body {
    position: relative;
    background: var(--stage);
    font-family: "Roboto", Arial, sans-serif;
  }
  .card {
    position: absolute;
    left: 313px;
    width: 600px;
    height: 343px;
    overflow: hidden;
  }
  .card--front { top: 113px; background: var(--paper); }
  .card--back { top: 472px; background: var(--black); }

  .front-shape { position: absolute; inset: 0; }

  .accent-tab {
    position: absolute;
    left: 0; top: 194px;
    width: 16px; height: 40px;
    background: var(--white);
  }

  .contact-list {
    position: absolute;
    left: 35px; top: 102px;
    list-style: none;
    color: var(--white);
    font-size: 14px;
    line-height: 19px;
  }
  .contact-list li { display: flex; align-items: center; white-space: nowrap; }
  .contact-list__web { font-size: 13px; }
  .contact-icon { width: 13px; height: 13px; margin-right: 9px; fill: var(--white); flex: none; }

  .person { position: absolute; left: 33px; top: 194px; color: var(--white); }
  .person__name {
    font-family: "Roboto Condensed", "Arial Narrow", sans-serif;
    font-weight: 700;
    font-size: 21px;
    line-height: 24px;
  }
  .person__title { font-size: 14px; font-weight: 500; line-height: 18px; }
  .person__rule { width: 22px; height: 1px; background: var(--white); margin: 5px 0 3px; }
  .person__email { font-size: 14px; line-height: 18px; white-space: nowrap; }
  .person__address { margin-top: 13px; font-size: 14px; line-height: 18px; }

  .brand-name {
    position: absolute;
    font-family: "Roboto Condensed", "Arial Narrow", sans-serif;
    font-weight: 700;
    text-align: center;
    text-transform: uppercase;
  }
  .brand-name--front {
    left: 340px; width: 250px; top: 58px;
    color: var(--ink);
    font-size: 34px; line-height: 38px;
    letter-spacing: 1px;
  }
  .brand-name--front .brand-name__sub { font-size: 17px; line-height: 26px; letter-spacing: 4px; display: block; }
  .brand-name--back {
    left: 0; width: 600px; top: 100px;
    color: var(--grey-light);
    font-size: 48px; line-height: 54px;
    letter-spacing: 2px;
  }
  .brand-name--back .brand-name__sub { font-size: 22px; line-height: 40px; letter-spacing: 5px; display: block; }

  .back-url {
    position: absolute;
    left: 0; width: 600px; top: 290px;
    text-align: center;
    color: var(--white);
    font-size: 13px;
    letter-spacing: 3px;
  }
</style>
</head>
<body>
  <section class="card card--front" aria-label="Business card front">
    <svg class="front-shape" width="600" height="343" viewBox="0 0 600 343" aria-hidden="true">
      <path d="M0,44 C80,28 170,34 236,74 C170,50 90,48 0,60 Z" fill="var(--grey-mid)"/>
      <path d="M0,65 C160,40 370,150 393,343 L0,343 Z" fill="var(--black)"/>
    </svg>
    <div class="accent-tab"></div>

    <ul class="contact-list">
      <li>
        <svg class="contact-icon" viewBox="0 0 16 16" aria-hidden="true"><path d="M3.5 1.5l2.5 0 1.2 3.2-1.6 1.3c.8 1.8 2.3 3.3 4.1 4.1l1.3-1.6 3.2 1.2v2.5c0 .9-.7 1.6-1.6 1.6C6.9 13.8 2 8.9 2 3.1c0-.9.7-1.6 1.5-1.6z"/></svg>
        919.362.4178
      </li>
      <li>
        <svg class="contact-icon" viewBox="0 0 16 16" aria-hidden="true"><path d="M4 0h8a1 1 0 0 1 1 1v14a1 1 0 0 1-1 1H4a1 1 0 0 1-1-1V1a1 1 0 0 1 1-1zm1 2v10h6V2zm3 11a1 1 0 1 0 0 2 1 1 0 0 0 0-2z"/></svg>
        919.537.2846
      </li>
      <li>
        <svg class="contact-icon" viewBox="0 0 16 16" aria-hidden="true"><path d="M4 1h8v4H4zM1 6h14v7h-3v2H4v-2H1zm4 5v3h6v-3z"/></svg>
        919.685.3907
      </li>
      <li class="contact-list__web">
        <svg class="contact-icon" viewBox="0 0 16 16" aria-hidden="true"><circle cx="8" cy="8" r="7"/><path d="M5 4c1 1 3 1 3 3s-2 1-2 3 1 2 1 4M10 3c0 2 2 2 2 4s-2 2-1 4" stroke="var(--black)" stroke-width="1.3" fill="none"/></svg>
        www.brightlinetattooremoval.example
      </li>
    </ul>

    <div class="person">
      <p class="person__name">MELISSA THORNBURY</p>
      <p class="person__title">Chief Executive Offer</p>
      <div class="person__rule"></div>
      <p class="person__email">mthornbury@brightlinetattooremoval.example</p>
      <p class="person__address">4615 Oakmere Pkwy, Suite 210<br>Raleigh, NC 27654</p>
    </div>

    <p class="brand-name brand-name--front">Brightline<span class="brand-name__sub">Tattoo Removal</span></p>
  </section>

  <section class="card card--back" aria-label="Business card back">
    <p class="brand-name brand-name--back">Brightline<span class="brand-name__sub">Tattoo Removal</span></p>
    <p class="back-url">www.brightlinetattooremoval.example</p>
  </section>
</body>
</html>
```